Veldmark Supplies Business Card

Professional business card that stand out to our potential customers. Front and back with clean modern design

Industry/Entity Type

Oil and gas

Contact Information for Business Card

Name, address, website , office phone and cell number

Requirements
Must have
• Editable files for each employee

```html
<!DOCTYPE html>
<html lang="en">
<head>
<meta charset="utf-8">
<title>Veldmark Supplies Business Card</title>
<link href="https://fonts.googleapis.com/css2?family=Montserrat:wght@800&family=Open+Sans:wght@400;600&display=swap" rel="stylesheet">
<style>
  :root {
    --cyan: #0fafd2;
    --red: #e8202a;
    --white: #ffffff;
    --ink: #1d1d1f;
    --stage: #2b2b2d;
  }
  * { box-sizing: border-box; margin: 0; padding: 0; }
  html, body { width: 1200px; height: 880px; overflow: hidden; }
  body {
    background: var(--stage);
    display: flex; flex-direction: column; align-items: center; justify-content: center;
    gap: 32px;
    font-family: "Open Sans", sans-serif;
  }
  .card {
    width: 680px; height: 388px; position: relative; overflow: hidden;
    box-shadow: 0 10px 30px rgba(0,0,0,.45);
  }
  .brand {
    display: flex; align-items: center; gap: 14px;
    font-family: "Montserrat", sans-serif; font-weight: 800;
    text-transform: uppercase; letter-spacing: .5px;
  }
  .brand-square { display: block; }

  /* Front */
  .card-front { background: var(--cyan); display: flex; align-items: center; justify-content: center; }
  .card-front .brand { color: var(--white); font-size: 34px; }
  .card-front .brand-square { width: 30px; height: 30px; background: var(--red); }

  /* Back */
  .card-back { background: var(--white); }
  .card-back .brand {
    position: absolute; left: 46px; top: 140px; width: 250px;
    color: var(--red); font-size: 25px; line-height: 1.15;
  }
  .card-back .brand-square { width: 26px; height: 26px; background: var(--cyan); flex: none; }
  .divider { position: absolute; top: 0; left: 0; }
  .wave { position: absolute; left: 0; bottom: 0; }

  .contact { position: absolute; left: 372px; top: 38px; color: var(--ink); }
  .contact-name {
    font-family: "Montserrat", sans-serif; font-weight: 800;
    color: var(--red); font-size: 24px; letter-spacing: .5px; text-transform: uppercase;
  }
  .contact-title { font-size: 15px; margin-bottom: 10px; }
  .contact-address { font-size: 15px; line-height: 1.3; margin-bottom: 8px; }
  .contact-list { list-style: none; font-size: 15px; }
  .contact-list li { display: flex; align-items: center; gap: 10px; height: 26px; }
  .icon { width: 20px; height: 20px; flex: none; }
  .accent { color: var(--red); }
</style>
</head>
<body>

<section class="card card-front" aria-label="Card front">
  <div class="brand"><span class="brand-square"></span>Veldmark Supplies</div>
</section>

<section class="card card-back" aria-label="Card back">
  <div class="brand"><span class="brand-square"></span><span>Veldmark<br>Supplies</span></div>

  <svg class="divider" width="680" height="388" viewBox="0 0 680 388" aria-hidden="true">
    <line x1="322" y1="70" x2="322" y2="262" stroke="var(--red)" stroke-width="2"/>
    <line x1="336" y1="52" x2="336" y2="282" stroke="var(--cyan)" stroke-width="2"/>
    <line x1="350" y1="84" x2="350" y2="250" stroke="var(--red)" stroke-width="2"/>
  </svg>

  <svg class="wave" width="680" height="388" viewBox="0 0 680 388" aria-hidden="true">
    <path d="M0 358 C 220 356, 360 332, 470 310 C 560 292, 620 288, 680 286 L680 388 L0 388 Z" fill="var(--cyan)"/>
    <path d="M0 352 C 220 350, 360 324, 470 301 C 560 282, 620 278, 680 276" fill="none" stroke="var(--red)" stroke-width="5"/>
    <path d="M0 355 C 220 353, 360 328, 470 306 C 560 287, 620 283, 680 281" fill="none" stroke="var(--white)" stroke-width="2"/>
  </svg>

  <div class="contact">
    <p class="contact-name">Dorin Kessler</p>
    <p class="contact-title">President</p>
    <p class="contact-address">2740 Harlow Ave, Ste<br>100, Midland, TX 79701</p>
    <ul class="contact-list">
      <li>
        <svg class="icon" viewBox="0 0 20 20" aria-hidden="true"><rect width="20" height="20" rx="3" fill="var(--red)"/><path d="M5 8 Q10 3 15 8 L13 9 Q10 7 7 9 Z M6 10 H14 V15 H6 Z" fill="var(--white)"/></svg>
        432-555-0148
      </li>
      <li>
        <svg class="icon" viewBox="0 0 20 20" aria-hidden="true"><rect width="20" height="20" rx="3" fill="var(--red)"/><rect x="6.5" y="3.5" width="7" height="13" rx="1.2" fill="none" stroke="var(--white)" stroke-width="1.6"/></svg>
        000-000-9999
      </li>
      <li>
        <svg class="icon" viewBox="0 0 20 20" aria-hidden="true"><rect width="20" height="20" rx="3" fill="var(--red)"/><rect x="4" y="6" width="12" height="8" fill="none" stroke="var(--white)" stroke-width="1.4"/><path d="M4 6 L10 11 L16 6" fill="none" stroke="var(--white)" stroke-width="1.4"/></svg>
        info@example-youremail.com
      </li>
      <li>
        <svg class="icon" viewBox="0 0 20 20" aria-hidden="true"><rect width="20" height="20" rx="3" fill="var(--red)"/><circle cx="10" cy="10" r="5.5" fill="none" stroke="var(--white)" stroke-width="1.4"/><path d="M4.5 10 H15.5 M10 4.5 V15.5" stroke="var(--white)" stroke-width="1.2"/></svg>
        <span>www.<span class="accent">example-yourwebsite</span>.com</span>
      </li>
    </ul>
  </div>
</section>

</body>
</html>
```